Redesign of an existing homepage

This site needs a redesign
https://www.wanderhof-kelbach.de
This page with the accommodation options is important for the customer
https://www.wanderhof-kelbach.de/gastgeber/
Till now there is a new logo. See attachment. That's all I have.
It would make sense to use the colors of the logo in the redesign.
footer.jpg.
I would put this info into the footer. The graphic (Infomaterial) is not needed.
a new menu - links.jpg
This info can be put in a new menu. Therefore the right column is gone and there is more space for the design.
NEW:
Please keep in mind that the Icons are important and shall be displayed under every accommodation

```html
<!DOCTYPE html>
<html lang="en">
<head>
<meta charset="utf-8">
<title>Tourismusverband Kelbachtal – Holiday in the Rottal</title>
<link href="https://fonts.googleapis.com/css2?family=Open+Sans:wght@300;400;600;700&display=swap" rel="stylesheet">
<style>
:root{
  --blue:#1f8ad0;
  --blue-dark:#1768a6;
  --green:#5aa832;
  --green-light:#8cc63f;
  --text:#333;
  --muted:#666;
  --grey-bg:#efefef;
  --white:#fff;
  --footer:#2a86c6;
}
*{box-sizing:border-box;margin:0;padding:0}
html,body{width:1200px;height:4340px;overflow:hidden}
body{font-family:"Open Sans",Arial,sans-serif;color:var(--text);background:var(--white);position:relative}
a{color:inherit;text-decoration:none}
section,header,footer{position:relative;width:1200px;overflow:hidden}

/* header */
.site-header{height:150px;background:var(--white);z-index:3}
.brand{position:absolute;left:28px;top:18px;display:flex;align-items:center;gap:14px}
.brand-mark{display:block;width:70px;height:70px;border-radius:50%;background:var(--blue);flex:none}
.brand-name{font-weight:700;color:var(--blue);font-size:20px;line-height:1.15;letter-spacing:.5px;text-transform:uppercase}
.partners{position:absolute;right:30px;top:10px;display:flex;gap:30px;align-items:center}
.partner-badge{width:150px;height:70px;background:#e8eef3;border-radius:6px}
.partner-badge.round{width:80px;height:80px;border-radius:50%;background:#cfe6b8}
.main-nav{position:absolute;right:0;top:112px;height:34px;width:840px;background:linear-gradient(90deg,#e6f2dc,#f4f9ef);display:flex;align-items:center;padding-left:10px;gap:6px}
.main-nav a{font-size:14px;font-weight:600;color:var(--blue-dark);padding:6px 16px}
.main-nav a.active{background:var(--green);color:var(--white);border-radius:3px}

/* hero */
.hero{height:670px;margin-top:-10px}
.hero-photo{position:absolute;inset:0;background:linear-gradient(180deg,#6fa6d8 0%,#a9c7dd 30%,#c9a87f 60%,#8e6c4d 100%)}
.hero-title{position:absolute;left:0;right:0;top:190px;text-align:center;color:var(--white);font-size:58px;font-weight:700;line-height:1.2;text-shadow:0 3px 8px rgba(0,0,0,.45)}
.btn{display:inline-flex;align-items:center;gap:12px;background:var(--green);color:var(--white);font-size:14px;font-weight:600;border-radius:22px;padding:0 6px 0 22px;height:40px}
.btn .btn-icon{width:30px;height:30px;border-radius:50%;background:var(--blue);display:flex;align-items:center;justify-content:center}
.hero .btn{position:absolute;left:516px;top:560px}
.hero-wave{position:absolute;left:0;bottom:0;width:1200px;height:90px}

/* about */
.about{height:520px}
.about-art{position:absolute;left:140px;top:60px;width:300px;height:300px;border-radius:50%;background:linear-gradient(160deg,#bfe0f4 0%,#e9f5e0 55%,#7cbf4a 100%);border:6px solid #e8f1f8}
.about-body{position:absolute;left:640px;top:80px;width:400px}
.section-title{font-size:48px;font-weight:400;color:var(--text)}
.section-title span{color:var(--blue)}
.about .section-title{font-size:46px}
.about-lead{color:var(--green);font-weight:600;font-size:16px;margin:10px 0 8px}
.about-text{font-size:15px;line-height:1.6;color:var(--muted)}
.about .btn{margin-top:28px}

/* discover */
.discover{height:590px;background:var(--grey-bg)}
.discover-title{position:absolute;left:0;right:0;top:40px;text-align:center;font-size:46px;font-weight:400;line-height:1.25}
.discover-title strong{color:var(--blue);font-weight:600;display:block}
.carousel{position:absolute;left:110px;top:205px;display:flex;gap:20px}
.place-card{width:235px;height:310px;border-radius:6px;overflow:hidden;background:var(--white);box-shadow:0 2px 8px rgba(0,0,0,.12);position:relative}
.place-photo{height:260px}
.place-card p{position:absolute;bottom:14px;left:0;right:0;text-align:center;font-size:15px;color:var(--text)}
.arrow{position:absolute;width:30px;height:30px;border-radius:50%;background:var(--blue);display:flex;align-items:center;justify-content:center}
.discover .arrow.left{left:40px;top:345px}
.discover .arrow.right{right:40px;top:345px;background:#bbb}

/* hosts */
.hosts{height:760px}
.hosts-head{position:absolute;left:108px;right:108px;top:80px;display:flex;justify-content:space-between;align-items:center}
.hosts-head .section-title{font-size:44px}
.host-grid{position:absolute;left:108px;top:180px;display:flex;gap:22px}
.host-card{width:314px;height:440px;border-radius:6px;box-shadow:0 2px 10px rgba(0,0,0,.14);overflow:hidden;background:var(--white)}
.host-photo{height:220px}
.host-info{padding:14px 16px}
.host-info h3{font-size:18px;font-weight:600}
.host-addr{font-size:12px;color:var(--muted);margin:6px 0 8px;display:flex;gap:6px;align-items:center}
.price{font-size:12px;color:var(--muted)}
.price b{color:var(--green);font-size:22px;font-weight:600}
.amen-label{color:var(--green);font-weight:600;font-size:13px;margin:8px 0 4px}
.amen{font-size:12px;line-height:1.55;color:var(--muted)}

/* video */
.video{height:510px}
.video-photo{position:absolute;inset:0;background:linear-gradient(180deg,#b9c7d4 0%,#c8b8a2 45%,#8a8279 100%)}
.play{position:absolute;left:570px;top:215px;width:60px;height:44px;border-radius:10px;background:#d93b2f;display:flex;align-items:center;justify-content:center}

/* news */
.news{height:660px}
.news .section-title{position:absolute;left:0;right:0;top:60px;text-align:center;font-size:46px;font-weight:600}
.news-grid{position:absolute;left:110px;top:160px;display:flex;gap:24px}
.news-card{width:310px}
.news-photo{height:270px;border-radius:6px}
.news-card h4{color:var(--green);font-size:18px;font-weight:600;margin-top:16px}
.news-card p{font-size:17px;margin-top:4px}
.news-card small{display:block;font-size:13px;color:var(--muted);margin-top:30px}
.news .arrow.left{left:40px;top:280px}
.news .arrow.right{right:40px;top:280px;background:#bbb}

/* footer */
.site-footer{height:480px;background:var(--footer);color:var(--white)}
.footer-wave{position:absolute;left:0;top:0;width:1200px;height:70px}
.footer-col{position:absolute;top:110px}
.footer-col h5{font-size:24px;font-weight:600;margin-bottom:16px}
.quick-links{left:108px}
.quick-links li{list-style:none;font-size:15px;line-height:28px}
.footer-brand{left:470px;top:90px;width:260px;text-align:center}
.footer-brand .brand-mark{width:90px;height:90px;background:var(--white);margin:0 auto 12px}
.footer-brand .brand-name{display:block;color:var(--white);font-size:22px}
.hours{font-size:13px;margin-top:20px;line-height:1.7}
.contact{left:820px;width:300px}
.contact li{list-style:none;display:flex;gap:12px;align-items:flex-start;font-size:13px;line-height:1.5;margin-bottom:14px}
.contact .ico{flex:none;width:26px;height:26px;border-radius:50%;background:var(--white);display:flex;align-items:center;justify-content:center}
.footer-bottom{position:absolute;left:0;right:0;bottom:0;height:44px;border-top:1px solid rgba(255,255,255,.35);display:flex;justify-content:space-between;align-items:center;padding:0 100px;font-size:12px}
</style>
</head>
<body>

<header class="site-header">
  <a class="brand" href="https://www.wanderhof-kelbach.de">
    <span class="brand-mark"></span>
    <span class="brand-name">Tourismusverband<br>Kelbachtal</span>
  </a>
  <div class="partners">
    <span class="partner-badge"></span>
    <span class="partner-badge"></span>
    <span class="partner-badge"></span>
    <span class="partner-badge round"></span>
  </div>
  <nav class="main-nav">
    <a class="active" href="https://www.wanderhof-kelbach.de">Home</a>
    <a href="https://www.wanderhof-kelbach.de/gastgeber/">Host</a>
    <a href="#">Rottal</a>
    <a href="#">Leisure time</a>
    <a href="#">Excursion destinations</a>
    <a href="#">Art and Culture</a>
    <a href="#">Contact</a>
  </nav>
</header>

<section class="hero">
  <div class="hero-photo" role="img" aria-label="Old town street with colourful houses and a tower gate under blue sky"></div>
  <h1 class="hero-title">Holiday in the Rottal -<br>the most beautiful spot<br>in Bavaria</h1>
  <a class="btn" href="#">Get Started <span class="btn-icon"><svg width="14" height="14" viewBox="0 0 14 14"><path d="M4 2l5 5-5 5" stroke="#fff" stroke-width="2" fill="none"/></svg></span></a>
  <svg class="hero-wave" viewBox="0 0 1200 90" preserveAspectRatio="none"><path d="M0 60 Q300 10 600 50 T1200 30 V90 H0Z" fill="#5aa832" opacity=".8"/><path d="M0 75 Q300 30 600 65 T1200 50 V90 H0Z" fill="#fff"/></svg>
</section>

<section class="about">
  <div class="about-art" role="img" aria-label="Circular illustration of green rolling hills of the region"></div>
  <div class="about-body">
    <h2 class="section-title">About <span>Us</span></h2>
    <p class="about-lead">Dear visitors,</p>
    <p class="about-text">Kelbach and the surrounding area have everything that makes life worth living: culture and nature, joie de vivre and enjoyment, friendly and open-minded people. Whether churches, fountains or other architectural monuments – on a tour through the Rottal you can discover many loving details for yourself.</p>
    <a class="btn" href="#">Read More <span class="btn-icon"><svg width="14" height="14" viewBox="0 0 14 14"><path d="M4 2l5 5-5 5" stroke="#fff" stroke-width="2" fill="none"/></svg></span></a>
  </div>
</section>

<section class="discover">
  <h2 class="discover-title">Discover, experience and <strong>Enjoy the Rottal!</strong></h2>
  <span class="arrow left"><svg width="12" height="12" viewBox="0 0 12 12"><path d="M8 1L3 6l5 5" stroke="#fff" stroke-width="2" fill="none"/></svg></span>
  <div class="carousel">
    <div class="place-card"><div class="place-photo" role="img" aria-label="Parish church with white tower" style="background:linear-gradient(180deg,#8fbbe0,#e6e1d4 70%,#7aa556)"></div><p>Parish churches</p></div>
    <div class="place-card"><div class="place-photo" role="img" aria-label="Lake view at Postmünster" style="background:linear-gradient(180deg,#a9cdea,#5f93b8 60%,#6c8f4d)"></div><p>Postmünster</p></div>
    <div class="place-card"><div class="place-photo" role="img" aria-label="Town square of Eggenfelden" style="background:linear-gradient(180deg,#7fb4e3,#d7c59f 60%,#9a8a6f)"></div><p>Eggenfelden</p></div>
    <div class="place-card"><div class="place-photo" role="img" aria-label="Baroque church of Schönau" style="background:linear-gradient(180deg,#5e9ad8,#e8d7b3 60%,#c9a76a)"></div><p>Schönau</p></div>
  </div>
  <span class="arrow right"><svg width="12" height="12" viewBox="0 0 12 12"><path d="M4 1l5 5-5 5" stroke="#fff" stroke-width="2" fill="none"/></svg></span>
</section>

<section class="hosts">
  <div class="hosts-head">
    <h2 class="section-title">Our <span>Host in the Rottal</span></h2>
    <a class="btn" href="https://www.wanderhof-kelbach.de/gastgeber/">View All <span class="btn-icon"><svg width="14" height="14" viewBox="0 0 14 14"><path d="M4 2l5 5-5 5" stroke="#fff" stroke-width="2" fill="none"/></svg></span></a>
  </div>
  <div class="host-grid">
    <article class="host-card">
      <div class="host-photo" role="img" aria-label="White farmhouse with courtyard" style="background:linear-gradient(180deg,#c5d6e4,#e9e8e2 55%,#9a9a92)"></div>
      <div class="host-info">
        <h3>Farm holidays</h3>
        <p class="host-addr"><svg width="10" height="13" viewBox="0 0 10 13"><path d="M5 0a5 5 0 0 1 5 5c0 3-5 8-5 8S0 8 0 5a5 5 0 0 1 5-5z" fill="#5aa832"/></svg>Wiesenweg 3, 84999 Kelbach</p>
        <p class="price">from <b>€ 40.00</b> per person</p>
        <p class="amen-label">Amenities</p>
        <p class="amen">Affordable family breakfast | Gluten-free breakfast | Bread roll service | Apartments with garden view | Yard toys with the owner | Camping on the farm | Playground on site | Cot</p>
      </div>
    </article>
    <article class="host-card">
      <div class="host-photo" role="img" aria-label="Farm with horses on a meadow" style="background:linear-gradient(180deg,#9ec4e6,#cfd8c0 50%,#6f9a46)"></div>
      <div class="host-info">
        <h3>Ferienhof Lindner</h3>
        <p class="host-addr"><svg width="10" height="13" viewBox="0 0 10 13"><path d="M5 0a5 5 0 0 1 5 5c0 3-5 8-5 8S0 8 0 5a5 5 0 0 1 5-5z" fill="#5aa832"/></svg>Feldweg 5, 84998 Wiesenheim</p>
        <p class="price">from <b>€ 70.00</b> for 2 people</p>
        <p class="amen-label">Amenities</p>
        <p class="amen">Bicycle rental | E-bike rental | Washing machine | Table tennis | Campfire with stick bread | Kids trampoline | Night hike | Baby equipment</p>
      </div>
    </article>
    <article class="host-card">
      <div class="host-photo" role="img" aria-label="Aerial view of a farmstead among green fields" style="background:linear-gradient(180deg,#7fae58,#a8c77c 50%,#5d8a3b)"></div>
      <div class="host-info">
        <h3>Moosbauer Hof</h3>
        <p class="host-addr"><svg width="10" height="13" viewBox="0 0 10 13"><path d="M5 0a5 5 0 0 1 5 5c0 3-5 8-5 8S0 8 0 5a5 5 0 0 1 5-5z" fill="#5aa832"/></svg>Lindenhof 2, 84997 Bachtal</p>
        <p class="price">from <b>€ 48.00</b></p>
        <p class="amen-label">Amenities</p>
        <p class="amen">Table tennis | Baby cot and highchair | 2 spaces for cars | Bicycle rental | Bicycle storage | Farm shop</p>
      </div>
    </article>
  </div>
</section>

<section class="video">
  <div class="video-photo" role="img" aria-label="Town square with a horse statue in front of historic buildings"></div>
  <span class="play"><svg width="18" height="18" viewBox="0 0 18 18"><path d="M4 2l12 7-12 7z" fill="#fff"/></svg></span>
</section>

<section class="news">
  <h2 class="section-title">Latest <span>News</span></h2>
  <span class="arrow left"><svg width="12" height="12" viewBox="0 0 12 12"><path d="M8 1L3 6l5 5" stroke="#fff" stroke-width="2" fill="none"/></svg></span>
  <div class="news-grid">
    <article class="news-card"><div class="news-photo" role="img" aria-label="Hot air balloon in a blue sky" style="background:linear-gradient(180deg,#6aa7e0,#b5d4ef 60%,#d85a4a)"></div><h4>Ballon Rides</h4><p>Discover the Rottal from above</p><small>Read More...</small></article>
    <article class="news-card"><div class="news-photo" role="img" aria-label="Horse riders on a green meadow" style="background:linear-gradient(180deg,#a3c8e6,#9cbf6e 55%,#5e8c38)"></div><h4>Ride</h4><p>Equestrian sports in the Rottal</p><small>Read More...</small></article>
    <article class="news-card"><div class="news-photo" role="img" aria-label="Thermal bath pool in summer" style="background:linear-gradient(180deg,#9fcde9,#e3d7bd 50%,#4fb0d6)"></div><h4>Thermal Baths</h4><p>The Rottal spa triangle</p><small>Read More...</small></article>
  </div>
  <span class="arrow right"><svg width="12" height="12" viewBox="0 0 12 12"><path d="M4 1l5 5-5 5" stroke="#fff" stroke-width="2" fill="none"/></svg></span>
</section>

<footer class="site-footer">
  <svg class="footer-wave" viewBox="0 0 1200 70" preserveAspectRatio="none"><path d="M0 0 H1200 V20 Q900 60 600 30 T0 40Z" fill="#fff"/></svg>
  <div class="footer-col quick-links">
    <h5>Quick Links</h5>
    <ul>
      <li>Home</li><li>Host</li><li>Rottal</li><li>Leisure time</li><li>Excursion destinations</li><li>Art and Culture</li><li>Contact</li>
    </ul>
  </div>
  <div class="footer-col footer-brand">
    <span class="brand-mark"></span>
    <span class="brand-name">Tourismusverband<br>Kelbachtal</span>
    <p class="hours">Mo–Fr &nbsp; 8:30 – 17:30 Uhr<br>Sa &nbsp; 10:00 – 13:00 Uhr</p>
  </div>
  <div class="footer-col contact">
    <h5>Contact Info</h5>
    <ul>
      <li><span class="ico"><svg width="10" height="13" viewBox="0 0 10 13"><path d="M5 0a5 5 0 0 1 5 5c0 3-5 8-5 8S0 8 0 5a5 5 0 0 1 5-5z" fill="#2a86c6"/></svg></span>Tourismusverband Kelbachtal und Umgebung e.V.<br>Marktgasse 7 · 84999 Kelbach</li>
      <li><span class="ico"><svg width="12" height="12" viewBox="0 0 12 12"><path d="M2 1h3l1 3-2 1a7 7 0 0 0 3 3l1-2 3 1v3c-6 0-9-3-9-9z" fill="#2a86c6"/></svg></span>0851 555 0140</li>
      <li><span class="ico"><svg width="12" height="12" viewBox="0 0 12 12"><rect x="2" y="3" width="8" height="7" fill="#2a86c6"/></svg></span>0851 555 0148</li>
      <li><span class="ico"><svg width="12" height="10" viewBox="0 0 12 10"><rect x="0.5" y="0.5" width="11" height="9" fill="none" stroke="#2a86c6"/><path d="M1 1l5 4 5-4" stroke="#2a86c6" fill="none"/></svg></span>info@wanderhof-kelbach.de</li>
    </ul>
  </div>
  <div class="footer-bottom">
    <span>2021 © Tourismusverband Kelbachtal. All Rights Reserved</span>
    <span>Informationen &nbsp; Impressum &nbsp; Datenschutzerklärung</span>
  </div>
</footer>

</body>
</html>
```